TINPAILFOLK.COM NEEDS FACELIFT!!!

Please see www.tinpailfolk.com for the basics. I am a glass artist who sells to retail market (art shows and e-commerce) as well as wholsale to art galleries nation wide. My site needs to serve both types of customer. I did the basics years ago, but now it's old and outdated . I need to totally rework the site, adding functionality as well as a new look.
My criteria are:
1. Need e-commerce page (cart) that allows for the rapid uploading of new artwork for my retail market.
2. Need separate login/e-commerce page for my wholesale customers as well as different pricing.
3. Need zip code lookup to show locations of current galleries.
4. Need registration page to collect customer emails/addresses for net marketing (brisk bulletin).
5. Design should be neutral background since I want to highlight to vivid colors of my work.
6. Site should be easy to navigate.
7. I need to have control of adding content to site as needed (new photos, events, etc.)
8. Need page to list upcoming schedule and event dates.
9. Need all the pages and content from old site, with some revisions to be determined after general design is complete.
...Any suggestions on how to make my site more interesting and functional are welcomed!!
Updates
Added photos of newer work today, some of these should appear in high impact areas of the site,. DEan
Question to all...I just remembered that I have already search engine optimized my site using all the appropriate meta tags and photo names, text, etc. for the search terms "glass boxes" and "mosaic mirrors." I am number 1 in zoppo search results of these terms. I need this to not change. Will redesigning my site affect this?
Reason: Hello all, I am in Rome italy right now on business and I have not had time to work with any of you on the designs yet. I am extending the deadline so I can provide more interaction . Dean
Reason: I am still traveling abroad and have no time to work with and review designs. I will be home on the 26th of Oct. then I will be more in touch. Dean
Target Market(s)
mid to high income women
Industry/Entity Type
E-Commerce
Requirements
Must have
- Separate shopping carts for retail and wholesale customers. Wholesale section requires login page.
Lots of pictures of my work. (will supply)
ZIP locator
Broken box repairs page. Customer describes broken piece and can buy replacement part. (size, color, knob color. Can provide pics of all the choices.)
Customer registration page to collect address and email for brisk bulletin or direct mailing.
I like a black or dark gray background of some sort, unless you have a better idea to make my work stand out
Nice to have
- Some kind of link in to social media sites would be great!!!
Should not have
- keep the layout very simple and easy to navigate. Don't want a confusing page

```html
<!DOCTYPE html>
<html lang="en">
<head>
<meta charset="utf-8">
<title>Tin Pail Folk – Glass Boxes and Mosaic Mirrors</title>
<link href="https://fonts.googleapis.com/css2?family=Arimo:wght@400;700&family=Oswald:wght@300;400&family=Stardos+Stencil:wght@700&display=swap" rel="stylesheet">
<style>
:root{
  --page-bg:#e4e4e4;
  --panel:#ffffff;
  --accent:#f7a600;
  --accent-light:#ffc632;
  --text:#333333;
  --muted:#a8a8a8;
  --line:#9a9a9a;
  --price:#f29b00;
  --footer-dark:#1d1d1d;
  --footer-text:#cfcfcf;
  --social-blue:#3d6fb3;
  --social-sky:#4aa8d8;
  --social-navy:#2f74b0;
  --social-orange:#e8762b;
}
*{margin:0;padding:0;box-sizing:border-box}
html,body{width:775px;height:1200px;overflow:hidden}
body{position:relative;background:linear-gradient(#d9d9d9 0,#f2f2f2 110px,#e9e9e9 460px,#e9e9e9 100%);font-family:Arimo,Arial,sans-serif;color:var(--text)}
.abs{position:absolute}
.page{left:36px;top:95px;width:702px;height:977px;background:var(--panel)}
.header{left:36px;top:0;width:702px;height:95px;background:linear-gradient(#000,#1a1a1a 70%,#333)}
.logo{left:47px;top:22px;font-weight:700;font-size:30px;color:var(--accent-light);letter-spacing:.5px}
.top-nav{right:6px;top:12px;font-size:9px;color:#ddd;display:flex}
.top-nav a{color:#ddd;text-decoration:none;padding:0 10px;border-left:1px solid #555}
.top-nav a:first-child{border:0;color:var(--accent)}
.cart-line{left:552px;top:38px;font-size:9px;color:#fff;display:flex;align-items:center;gap:8px}
.cart-line b{color:var(--accent)}
.tagline{left:297px;top:70px;font-size:9px;color:#fff}
.search{left:520px;top:66px;width:180px;height:30px;background:#e6e6e6;border-radius:6px 6px 0 0}
.search .field{left:7px;top:6px;width:130px;height:23px;background:#fff;border:1px solid #ddd}
.search .go{left:139px;top:6px;width:24px;height:23px;background:var(--accent)}
.hero{left:44px;top:120px;width:688px;height:300px;background:radial-gradient(ellipse at 50% 45%,#fff 0,#f4f4f4 60%,#e6e6e6 100%)}
.hero-art{left:66px;top:10px;width:386px;height:265px;border-radius:10px 10px 40px 40px;
  background:
    radial-gradient(circle at 30% 30%,rgba(40,70,180,.85) 0,rgba(40,70,180,0) 22%),
    radial-gradient(circle at 72% 22%,rgba(220,170,40,.9) 0,rgba(220,170,40,0) 22%),
    radial-gradient(circle at 72% 48%,rgba(200,30,40,.9) 0,rgba(200,30,40,0) 24%),
    radial-gradient(circle at 30% 55%,rgba(110,60,160,.9) 0,rgba(110,60,160,0) 24%),
    radial-gradient(circle at 78% 75%,rgba(170,210,60,.95) 0,rgba(170,210,60,0) 28%),
    radial-gradient(circle at 32% 80%,rgba(230,160,30,.85) 0,rgba(230,160,30,0) 22%),
    linear-gradient(160deg,#5f8f8a 0,#2f5f60 45%,#1e3436 100%)}
.hero h2{left:452px;top:40px;width:200px;text-align:center;font-family:"Stardos Stencil",serif;font-size:16px;line-height:26px;color:#3a3a3a;letter-spacing:.5px}
.hero p{left:465px;top:99px;width:168px;font-size:12.5px;line-height:17.5px;color:#444}
.btn-shop{left:501px;top:187px;width:102px;height:28px;border-radius:4px;background:linear-gradient(var(--accent-light),var(--accent));color:#fff;font-weight:700;font-size:15px;text-align:center;line-height:28px}
.dots{left:626px;top:281px;display:flex;gap:3px}
.dots i{width:7px;height:7px;border-radius:50%;background:#d6d6d6;display:block}
.dots i.on{background:#777}
.arrow{top:128px}
.side-box{left:65px;width:164px;border:1px solid #d6d6d6;border-radius:4px;background:#fff}
.links{top:435px;height:313px}
.links h3{height:29px;border-radius:4px 4px 0 0;background:linear-gradient(#ffc632,#f29b00);color:#fff;font-weight:400;font-size:14px;padding:6px 17px;letter-spacing:.5px}
.links ul{list-style:none;padding:4px 0 0 21px}
.links li{height:22.5px;font-size:10.5px;display:flex;align-items:center;gap:12px;color:#333}
.links li i{width:11px;height:11px;border-radius:50%;background:#e7e7e7;display:block}
.links li.on i{background:var(--accent)}
.best{top:757px;height:300px}
.best h3{height:29px;background:linear-gradient(#f2f2f2,#dedede);font-weight:400;font-size:13px;text-align:center;line-height:29px;color:#333}
.best .art{left:0;top:29px;width:162px;height:219px;
  background:
    radial-gradient(ellipse 22% 55% at 50% 55%,rgba(120,130,110,.95) 0,rgba(120,130,110,0) 100%),
    radial-gradient(ellipse 18% 22% at 50% 80%,rgba(150,80,60,.8) 0,rgba(150,80,60,0) 100%),
    linear-gradient(#0d0d0d 0,#2a2c2a 45%,#8a8c8a 80%,#eeeeee 100%)}
.small-copy{font-size:8px;line-height:10.5px;color:var(--muted)}
.best .small-copy{left:10px;top:258px;width:130px}
.best .price{left:120px;top:285px;font-size:9px;color:var(--price);font-weight:700}
.new-title{left:268px;top:441px;font-size:14px;color:#333;font-weight:400}
.products{left:255px;top:470px;width:463px;height:583px;border:1px solid var(--line);border-radius:4px}
.products .row-line{left:0;top:292px;width:100%;border-top:1px solid var(--line)}
.vdiv{width:0;border-left:1px dotted #999}
.product .photo{width:138px;height:161px;border-radius:3px}
.photo.p1{background:
  radial-gradient(circle at 45% 30%,rgba(60,160,90,.9) 0,rgba(60,160,90,0) 25%),
  radial-gradient(circle at 35% 60%,rgba(60,150,210,.9) 0,rgba(60,150,210,0) 28%),
  radial-gradient(circle at 75% 80%,rgba(220,50,30,.9) 0,rgba(220,50,30,0) 26%),
  radial-gradient(circle at 70% 55%,rgba(230,120,40,.8) 0,rgba(230,120,40,0) 22%),
  linear-gradient(#07080c,#1a2030 70%,#e6e6e6 100%)}
.photo.p2{background:
  radial-gradient(circle at 50% 20%,rgba(90,190,190,.9) 0,rgba(90,190,190,0) 20%),
  radial-gradient(circle at 45% 45%,rgba(60,110,200,.9) 0,rgba(60,110,200,0) 24%),
  radial-gradient(circle at 55% 65%,rgba(230,70,40,.85) 0,rgba(230,70,40,0) 22%),
  radial-gradient(circle at 50% 85%,rgba(120,190,180,.9) 0,rgba(120,190,180,0) 28%),
  linear-gradient(#080a14,#1a2036 70%,#dfe6ea 100%)}
.photo.p3{background:
  radial-gradient(circle at 35% 35%,rgba(60,120,200,.95) 0,rgba(60,120,200,0) 30%),
  radial-gradient(circle at 80% 35%,rgba(200,60,80,.8) 0,rgba(200,60,80,0) 22%),
  radial-gradient(ellipse 40% 20% at 45% 80%,rgba(140,200,80,.85) 0,rgba(140,200,80,0) 100%),
  linear-gradient(#120a10,#2a1e28 60%,#f0f0f0 100%)}
.photo.p4{background:
  radial-gradient(circle at 50% 20%,rgba(150,200,190,.9) 0,rgba(150,200,190,0) 26%),
  radial-gradient(circle at 45% 50%,rgba(200,170,110,.9) 0,rgba(200,170,110,0) 26%),
  radial-gradient(circle at 55% 82%,rgba(90,140,120,.9) 0,rgba(90,140,120,0) 28%),
  linear-gradient(#0a0c10,#1c2428 60%,#d8dcdc 100%)}
.product .small-copy{width:142px}
.product .price{font-size:12px;font-weight:700;color:var(--price)}
.btn{height:19px;font-size:8.5px;font-weight:700;line-height:19px;text-align:center;border-radius:2px}
.btn-cart{width:61px;background:#262626;color:#fff}
.btn-cart.hot{background:linear-gradient(#ffc632,#f29b00);color:#333}
.btn-details{width:44px;background:#e6e6e6;color:#333;font-weight:400}
.footer{left:0;top:1072px;width:775px;height:128px;background:var(--footer-dark)}
.fcol{top:0;height:128px}
.fcol h4{font-family:Oswald,sans-serif;font-weight:300;font-size:14px;color:#eee;letter-spacing:1.5px;text-align:center}
.fcol.schedule{left:38px;width:224px;background:#2e2e2e}
.fcol.connect{left:262px;width:250px;background:#262626}
.fcol.news{left:512px;width:224px;background:#2e2e2e}
.fcol p{font-size:8.5px;color:var(--footer-text)}
.social{display:flex;gap:11px;left:73px;top:45px}
.social i{width:18px;height:18px;border-radius:50%;display:block;border:2px solid #e8e8e8;box-shadow:0 1px 2px rgba(0,0,0,.6)}
.social i.s1{background:radial-gradient(circle at 40% 35%,#6a98d8,var(--social-blue))}
.social i.s2{background:radial-gradient(circle at 40% 35%,#8fd0f0,var(--social-sky))}
.social i.s3{background:radial-gradient(circle at 40% 35%,#5a9ad0,var(--social-navy))}
.social i.s4{background:radial-gradient(circle at 40% 35%,#f6a060,var(--social-orange))}
.flinks{left:0;width:250px;top:80px;text-align:center;font-size:8.5px;color:var(--footer-text)}
.copyright{left:0;width:250px;top:102px;text-align:center;font-size:8.5px;color:var(--footer-text)}
.label{font-size:9px;color:#bbb;width:88px;text-align:right}
.input{width:100px;height:17px;background:#666}
.subscribe{left:104px;top:94px;width:74px;height:20px;border-radius:3px;background:linear-gradient(#3a3a3a,#111);color:var(--accent);font-size:9px;text-align:center;line-height:20px}
</style>
</head>
<body>
<div class="abs page"></div>

<header class="abs header">
  <div class="abs logo">Tin Pail Folk</div>
  <nav class="abs top-nav"><a>My Account</a><a>My Wishlist</a><a>My Cart</a><a>Checkout</a><a>Log In</a></nav>
  <div class="abs cart-line">
    <svg width="18" height="14" viewBox="0 0 18 14"><path d="M1 4h16l-2 9H3z" fill="none" stroke="#f7a600" stroke-width="1.6"/><path d="M5 4l4-3 4 3" fill="none" stroke="#f7a600" stroke-width="1.4"/></svg>
    <span>Now in your cart <b>0 items</b></span>
  </div>
  <div class="abs tagline">Glass Boxes and Mosaic Mirrors at Tin Pail Folk.</div>
  <div class="abs search">
    <div class="abs field"></div>
    <div class="abs go"><svg width="24" height="23" viewBox="0 0 24 23"><circle cx="11" cy="10" r="5" fill="none" stroke="#fff" stroke-width="2"/><path d="M14.5 13.5l4 4" stroke="#fff" stroke-width="2.4"/></svg></div>
  </div>
</header>

<section class="abs hero">
  <div class="abs hero-art" role="img" aria-label="Colourful glass chest with six patterned drawers and glass knobs"></div>
  <svg class="abs arrow" style="left:28px" width="22" height="32" viewBox="0 0 22 32"><path d="M18 3L5 16l13 13" fill="none" stroke="#111" stroke-width="5"/></svg>
  <svg class="abs arrow" style="left:645px" width="22" height="32" viewBox="0 0 22 32"><path d="M4 3l13 13L4 29" fill="none" stroke="#111" stroke-width="5"/></svg>
  <h2 class="abs">LOREM IPSUM DOLOR<br>SIT AMET</h2>
  <p class="abs">Lorem ipsum dolor sit amet, consectetuer adipiscing elit. Nam nibh. Nunc varius facilisis eros.</p>
  <div class="abs btn-shop">Shop Now!</div>
  <div class="abs dots"><i></i><i></i><i></i><i class="on"></i><i></i></div>
</section>

<aside class="abs side-box links">
  <h3>LINKS</h3>
  <ul>
    <li class="on"><i></i>Home</li><li><i></i>About the Artist</li><li><i></i>Glass Boxes</li><li><i></i>Mosaic Mirrors</li><li><i></i>Mosaic Tables</li><li><i></i>Other Photos</li><li><i></i>Store Locator</li><li><i></i>Shop Online</li><li><i></i>Show Schedule</li><li><i></i>Wholesale</li><li><i></i>Contact</li><li><i></i>Copycats!</li>
  </ul>
</aside>

<aside class="abs side-box best">
  <h3>BEST SELLERS</h3>
  <div class="abs art" role="img" aria-label="Tall tapered glass tower of stacked drawers"></div>
  <p class="abs small-copy">Laoreet dolore magnaorem ipsum dolor ser adipiscing elit, sed diam non neque. Fusce v...</p>
  <div class="abs price">$299.99</div>
</aside>

<h2 class="abs new-title">NEW PRODUCTS</h2>
<section class="abs products">
  <div class="abs row-line"></div>
  <div class="abs vdiv" style="left:226px;top:20px;height:160px"></div>
  <div class="abs vdiv" style="left:226px;top:312px;height:160px"></div>

  <div class="abs product" style="left:36px;top:20px">
    <div class="photo p1" role="img" aria-label="Stack of colourful glass drawer boxes"></div>
    <p class="small-copy" style="margin-top:11px">Laoreet dolore magnaorem ipsum dolor ser adipiscing elit, sed diam non aliquam neque. Fusce v...</p>
    <div class="price" style="margin-top:6px">$79.99</div>
    <div style="display:flex;gap:4px;margin-top:6px"><div class="btn btn-cart hot">Add to Cart</div><div class="btn btn-details">Details</div></div>
  </div>
  <div class="abs product" style="left:275px;top:20px">
    <div class="photo p2" role="img" aria-label="Tall tower of stacked glass drawer boxes"></div>
    <p class="small-copy" style="margin-top:15px">Laoreet dolore magnaorem ipsum dolor ser adipiscing elit, sed diam non aliquam neque. Fusce v...</p>
    <div class="price" style="margin-top:6px">$299.99</div>
    <div style="display:flex;gap:4px;margin-top:6px"><div class="btn btn-cart">Add to Cart</div><div class="btn btn-details">Details</div></div>
  </div>
  <div class="abs product" style="left:36px;top:311px">
    <div class="photo p3" role="img" aria-label="Blue patterned glass box on green legs"></div>
    <p class="small-copy" style="margin-top:11px">Laoreet dolore magnaorem ipsum dolor ser adipiscing elit, sed diam non aliquam neque. Fusce v...</p>
    <div class="price" style="margin-top:6px">$299.99</div>
    <div style="display:flex;gap:4px;margin-top:6px"><div class="btn btn-cart">Add to Cart</div><div class="btn btn-details">Details</div></div>
  </div>
  <div class="abs product" style="left:275px;top:311px">
    <div class="photo p4" role="img" aria-label="Stacked textured glass boxes with open drawers"></div>
    <p class="small-copy" style="margin-top:11px">Laoreet dolore magnaorem ipsum dolor ser adipiscing elit, sed diam non aliquam neque. Fusce v...</p>
    <div class="price" style="margin-top:6px">$299.99</div>
    <div style="display:flex;gap:4px;margin-top:6px"><div class="btn btn-cart">Add to Cart</div><div class="btn btn-details">Details</div></div>
  </div>
</section>

<footer class="abs footer">
  <div class="abs fcol schedule">
    <h4 style="margin-top:12px">UPCOMING SCHEDULE</h4>
    <svg class="abs" style="left:34px;top:68px" width="36" height="42" viewBox="0 0 36 42"><rect x="2" y="6" width="32" height="34" rx="3" fill="#eee"/><rect x="2" y="6" width="32" height="10" rx="3" fill="#c8302a"/><rect x="9" y="2" width="3" height="8" fill="#999"/><rect x="24" y="2" width="3" height="8" fill="#999"/><text x="18" y="35" font-family="Arimo,Arial,sans-serif" font-size="15" font-weight="700" text-anchor="middle" fill="#222">15</text></svg>
    <p class="abs" style="left:85px;top:73px;width:110px;line-height:11px">Lum mlecnean maurilra kerase meras soc totisenonlu sermerse</p>
    <p class="abs" style="left:85px;top:113px;color:var(--accent)">more</p>
  </div>
  <div class="abs fcol connect">
    <h4 style="margin-top:12px">CONNECT US</h4>
    <div class="abs social"><i class="s1"></i><i class="s2"></i><i class="s3"></i><i class="s4"></i></div>
    <div class="abs flinks">Privacy Policy &nbsp;| &nbsp; Terms &amp; Conditions &nbsp;| &nbsp; Contact us</div>
    <div class="abs copyright">© 2011 Tin Pail Folk, All Rights Reserved</div>
  </div>
  <div class="abs fcol news">
    <h4 style="margin-top:10px">NEWSLETTER</h4>
    <div class="abs label" style="left:0;top:42px">User Name :</div>
    <div class="abs input" style="left:101px;top:37px"></div>
    <div class="abs label" style="left:0;top:72px">Email Address :</div>
    <div class="abs input" style="left:101px;top:68px"></div>
    <div class="abs subscribe">Subscribe</div>
  </div>
</footer>
</body>
</html>
```